Wordpress Website Update - Elementor

I'm currently using Elementor and would like my site to be updated. A nice facelift to the current pages. We are a small boutique animation service company.
I have a list of similar production houses to use as references and would like the format/style of the site not to feel so corporate and infuse the fun that we bring to working with clients on animated projects.

Additionally, I'd like to add 2 more pages focusing on more portfolio work and Original IP - which is now our primary goal to sell our show ideas. Maybe have a password projected behind an image showcasing the show/ film. Go to our current site to review. www.pebblemoatfilms.com

Animation/ Commercials/ Vorlica/ Quelbar/ Durno/ KVT - Okay with first page being shorter and not as long as well. Have contact us 'above the fold' on options as well.

Animation and Film

• Current 3 pages - additional 2 - we can focus on layout and arrangement with temporary images then swap with real assets when ready.
• site examples: pirtolstudios.com, Mardle House, Fenra Studios, Gorbleck.net, Quillstone Animation, Brindlemop Animation Studios, ZaZe Studios use Varkel Plus as inspiration.

```html
<!DOCTYPE html>
<html lang="en">
<head>
<meta charset="utf-8">
<title>Pebblemoat Films – Animation Studio</title>
<link rel="stylesheet" href="https://fonts.googleapis.com/css2?family=Fredoka:wght@500;600&family=Lato:wght@400;700&display=swap">
<style>
:root{
  --ink:#1b1b1f;
  --body:#55555c;
  --white:#ffffff;
  --night:#141216;
  --navy:#15152a;
  --brand:#6a3fe0;
  --brand-soft:#8b6cf0;
  --lavender:#efeafd;
  --accent-red:#e0242c;
  --card-line:#9b85ea;
}
*{box-sizing:border-box;margin:0;padding:0}
html,body{width:1200px;height:4882px;overflow:hidden;background:var(--white)}
body{position:relative;font-family:"Lato",sans-serif;color:var(--body)}
.display{font-family:"Fredoka",sans-serif;font-weight:600;color:var(--ink);letter-spacing:.5px}
section,header,footer{position:absolute;left:0;width:1200px}
.abs{position:absolute}

/* hero */
.hero{top:0;height:735px;background:#000;overflow:hidden}
.hero-panels{display:flex;height:735px}
.hero-panel{flex:1;height:100%;border-right:4px solid #000}
.hero-panel:nth-child(1){background:
  radial-gradient(ellipse 60% 30% at 30% 45%,#8a4f2c 0,transparent 100%),
  radial-gradient(ellipse 70% 25% at 60% 75%,#2f6a8a 0,transparent 100%),
  linear-gradient(180deg,#7a9a5a 0,#a77a45 40%,#6a4a30 65%,#1e1e1e 100%)}
.hero-panel:nth-child(2){background:
  radial-gradient(ellipse 55% 30% at 55% 60%,#d8483e 0,transparent 100%),
  radial-gradient(ellipse 45% 20% at 50% 22%,#5a3a2a 0,transparent 100%),
  linear-gradient(180deg,#2f5f8f 0,#3a6fb0 35%,#7a2e3a 70%,#141418 100%)}
.hero-panel:nth-child(3){background:
  radial-gradient(ellipse 50% 40% at 50% 30%,#c79a5e 0,transparent 100%),
  radial-gradient(ellipse 40% 60% at 50% 75%,#8a6640 0,transparent 100%),
  linear-gradient(180deg,#6a6e6a 0,#4e4c48 50%,#1a1818 100%)}
.hero-panel:nth-child(4){background:
  radial-gradient(ellipse 50% 35% at 50% 35%,#d86ad0 0,transparent 100%),
  radial-gradient(ellipse 60% 30% at 40% 70%,#2a1a3a 0,transparent 100%),
  linear-gradient(180deg,#4a22b0 0,#8a34c8 40%,#2a1245 75%,#0e0818 100%)}
.hero-panel:nth-child(5){background:
  radial-gradient(ellipse 50% 30% at 55% 40%,#7ab8e0 0,transparent 100%),
  radial-gradient(ellipse 40% 30% at 50% 60%,#3a4a58 0,transparent 100%),
  linear-gradient(180deg,#4aa2dd 0,#2470a8 45%,#123a62 75%,#08182a 100%)}
.hero-shade{position:absolute;inset:0;background:linear-gradient(180deg,rgba(0,0,0,.3),rgba(0,0,0,0) 25%,rgba(0,0,0,0) 55%,rgba(0,0,0,.85))}
.site-nav{position:absolute;top:0;left:0;width:1200px;height:118px;border-bottom:1px solid rgba(255,255,255,.35)}
.brand{position:absolute;left:70px;top:40px;font-family:"Fredoka",sans-serif;font-weight:600;font-size:30px;color:var(--brand-soft);line-height:1}
.nav-links{position:absolute;top:54px;left:0;list-style:none}
.nav-links li{position:absolute;white-space:nowrap;font-size:14px;font-weight:700;color:var(--white);letter-spacing:.3px}
.caret{display:inline-block;margin-left:10px;width:6px;height:6px;border-right:1.5px solid #fff;border-bottom:1.5px solid #fff;transform:rotate(45deg) translateY(-3px)}
.slider-arrow{position:absolute;top:326px;width:38px;height:38px;border-radius:50%;background:rgba(10,10,10,.85)}
.dots{position:absolute;top:673px;left:536px;display:flex;gap:16px}
.dot{width:12px;height:12px;border-radius:50%;background:#cfcfcf}
.dot.active{background:var(--brand);box-shadow:0 0 0 3px #bfb0f5}

/* feature rows */
.eyebrow{font-size:19px;color:#3a3a40}
.title{font-size:31px;margin-top:18px}
.copy{font-size:16.5px;line-height:28px;margin-top:22px;color:var(--body)}
.more{font-size:13px;font-weight:700;color:var(--ink);letter-spacing:.6px;margin-top:24px;display:flex;align-items:center;gap:10px}
.text-right{text-align:right}
.text-right .more{justify-content:flex-end}
.media{position:absolute;box-shadow:inset 0 0 0 1px rgba(0,0,0,.08)}

.showcase{top:735px;height:914px;background:var(--white)}
.dark-band{top:1649px;height:510px;background:radial-gradient(circle at 30% 60%,#241f22,var(--night) 70%)}
.dark-band .eyebrow,.dark-band .title{color:var(--white)}
.dark-band .copy{color:#e6e6e6}
.btn{display:inline-block;background:var(--white);color:var(--ink);font-size:15px;font-weight:700;letter-spacing:.3px;padding:0 24px;line-height:63px;margin-top:30px}

/* projects */
.projects{top:2159px;height:792px;background:var(--white);text-align:center}
.section-eyebrow{font-size:19px;color:#3a3a40;position:absolute;width:100%;top:100px}
.section-title{font-size:31px;position:absolute;width:100%;top:148px}
.project-grid{position:absolute;left:112px;top:219px;width:974px;display:grid;grid-template-columns:repeat(4,233px);grid-auto-rows:222px;gap:19px 14px}
.tile{width:233px;height:222px}

/* cta */
.cta{top:2951px;height:508px;background:radial-gradient(circle at 60% 60%,#1f2346,var(--navy) 75%)}
.cta .eyebrow,.cta .title{color:var(--white)}
.cta .copy{color:#dedde8}

/* expertise */
.expertise{top:3459px;height:939px;background:var(--white);text-align:center}
.cards{position:absolute;left:112px;top:227px;width:974px;display:grid;grid-template-columns:repeat(3,292px);grid-template-rows:279px 289px;column-gap:49px;row-gap:39px}
.card{background:var(--white);box-shadow:0 2px 10px rgba(0,0,0,.12);border-bottom:4px solid var(--card-line);padding:30px 26px 0;text-align:center}
.card.is-active{border-bottom-color:var(--accent-red);box-shadow:0 4px 16px rgba(0,0,0,.2)}
.card-icon{height:92px;margin:0 auto;border-radius:18px;background:linear-gradient(160deg,#f3effe,#e2d9fb);border:2px solid #cfc3f6}
.card h3{font-size:19px;margin-top:20px}
.card p{font-size:12.5px;line-height:20px;color:#4a4a52;margin-top:12px}

/* footer */
.site-footer{top:4398px;height:484px;background:var(--navy);color:#e9e9f0}
.footer-brand{position:absolute;left:112px;top:112px;font-family:"Fredoka",sans-serif;font-weight:600;font-size:40px;color:var(--brand-soft);line-height:1}
.footer-about{position:absolute;left:112px;top:214px;width:290px;font-size:14.5px;line-height:27px}
.footer-col{position:absolute;top:118px;list-style:none}
.footer-col h4{font-family:"Fredoka",sans-serif;font-weight:500;font-size:19px;color:var(--brand);margin-bottom:12px}
.footer-col li{font-size:15px;line-height:40px}
.footer-rule{position:absolute;left:112px;top:366px;width:974px;height:1px;background:#4a4a66}
.copyright{position:absolute;left:112px;top:418px;font-size:13.5px}
.socials{position:absolute;left:906px;top:410px;display:flex;gap:17px}
.social{width:33px;height:33px;border-radius:50%;border:1.5px solid #e9e9f0}
</style>
</head>
<body>

<header class="hero">
  <div class="hero-panels">
    <div class="hero-panel" role="img" aria-label="Animated sheep on a painted landscape"></div>
    <div class="hero-panel" role="img" aria-label="Animated child playing a drum"></div>
    <div class="hero-panel" role="img" aria-label="Animated giraffe wearing glasses"></div>
    <div class="hero-panel" role="img" aria-label="Animated girl character on a purple stage"></div>
    <div class="hero-panel" role="img" aria-label="Animated diver underwater with fish"></div>
  </div>
  <div class="hero-shade"></div>
  <nav class="site-nav">
    <div class="brand">Pebblemoat</div>
    <ul class="nav-links">
      <li style="left:284px">HOME</li>
      <li style="left:385px">ABOUT US</li>
      <li style="left:521px">OUR EXPERTISE<span class="caret"></span></li>
      <li style="left:697px">PROJECTS<span class="caret"></span></li>
      <li style="left:832px">CONTACT US</li>
    </ul>
    <svg class="abs" style="left:1082px;top:56px" width="14" height="14" viewBox="0 0 14 14" fill="none" stroke="#fff" stroke-width="1.6"><circle cx="6" cy="6" r="4.5"/><path d="M9.5 9.5L13 13"/></svg>
    <svg class="abs" style="left:1136px;top:56px" width="20" height="14" viewBox="0 0 20 14" stroke="#fff" stroke-width="2"><path d="M0 1h20M0 7h20M0 13h20"/></svg>
  </nav>
  <div class="slider-arrow" style="left:30px"><svg width="38" height="38" viewBox="0 0 38 38" fill="none" stroke="#fff" stroke-width="2.4"><path d="M22 12l-7 7 7 7"/></svg></div>
  <div class="slider-arrow" style="left:1118px"><svg width="38" height="38" viewBox="0 0 38 38" fill="none" stroke="#fff" stroke-width="2.4"><path d="M16 12l7 7-7 7"/></svg></div>
  <div class="dots"><span class="dot"></span><span class="dot"></span><span class="dot active"></span><span class="dot"></span><span class="dot"></span></div>
</header>

<section class="showcase">
  <div class="abs text-right" style="left:112px;top:118px;width:449px">
    <div class="eyebrow">Animate</div>
    <h2 class="display title">ANiMATiON REEL</h2>
    <p class="copy">Story and Animation is where PMF thrives and yes there's a lot of outsourcing nowadays and you get what you pay for. So I can guarantee you get the best when you work with us.</p>
    <div class="more">VIEW MORE <svg width="22" height="10" viewBox="0 0 22 10" fill="none" stroke="#1b1b1f" stroke-width="1.3"><path d="M0 5h21M17 1l4 4-4 4"/></svg></div>
  </div>
  <div class="media" style="left:650px;top:116px;width:436px;height:282px;background:
    radial-gradient(ellipse 30% 30% at 25% 25%,#e27ad6 0,transparent 100%),
    radial-gradient(ellipse 30% 30% at 75% 25%,#e27ad6 0,transparent 100%),
    radial-gradient(ellipse 70% 25% at 50% 88%,#3a2a4a 0,transparent 100%),
    linear-gradient(180deg,#6a30c8 0,#8a3ed8 45%,#2a1652 80%,#1a1030 100%)" role="img" aria-label="Animated characters in suits on a purple stage with hearts"></div>

  <div class="media" style="left:112px;top:510px;width:436px;height:283px;background:
    radial-gradient(ellipse 25% 45% at 60% 55%,#b08a5a 0,transparent 100%),
    radial-gradient(ellipse 20% 30% at 88% 65%,#e6b876 0,transparent 100%),
    linear-gradient(90deg,#5a4a3e 0,#6a5646 25%,#2e2824 45%,#1e1a1a 100%)" role="img" aria-label="Animated giraffe with glasses in a study"></div>
  <div class="abs" style="left:650px;top:510px;width:440px">
    <div class="eyebrow">Fresh Out The Render Oven. Careful It's</div>
    <h2 class="display title">GiRAGGES &amp; KiDS ARE FREE!</h2>
    <p class="copy">Pebblemoat kicked major butt on this fun project. Read more about the role we played bringing this commercial to life. And yes there's a lot of outsourcing nowadays and you get what you pay for.</p>
    <div class="more"><svg width="22" height="10" viewBox="0 0 22 10" fill="none" stroke="#1b1b1f" stroke-width="1.3"><path d="M22 5H1M5 1L1 5l4 4"/></svg> VIEW MORE</div>
  </div>
</section>

<section class="dark-band">
  <div class="abs text-right" style="left:112px;top:100px;width:449px">
    <div class="eyebrow">The Sky's The Limit</div>
    <h2 class="display title">WE MAKE iT FUn</h2>
    <p class="copy">Did we mention we LOVE what we do? The industry has changed a lot over the years. And yes there's a lot of outsourcing nowadays and you get what you pay for.</p>
    <a class="btn">MORE DEMO REELS</a>
  </div>
  <div class="media" style="left:650px;top:106px;width:436px;height:298px;background:
    radial-gradient(ellipse 30% 40% at 30% 25%,#d8d2c4 0,transparent 100%),
    radial-gradient(ellipse 35% 25% at 42% 55%,#8a5a36 0,transparent 100%),
    radial-gradient(ellipse 20% 55% at 88% 55%,#c49660 0,transparent 100%),
    linear-gradient(180deg,#6e6a64 0,#4a4440 50%,#24323a 80%,#1a1a1e 100%)" role="img" aria-label="Video player showing animated animals on an ark"></div>
  <svg class="abs" style="left:670px;top:362px" width="396" height="26" viewBox="0 0 396 26">
    <rect width="396" height="26" rx="3" fill="#1a1a1e"/>
    <path d="M10 8l8 5-8 5z" fill="#fff"/>
    <rect x="30" y="11" width="256" height="4" fill="#555"/>
    <rect x="30" y="11" width="80" height="4" fill="#fff"/>
    <circle cx="300" cy="13" r="3" fill="#fff"/>
    <path d="M318 8h6M318 8v6M338 18h-6M338 18v-6" stroke="#fff" stroke-width="1.5" fill="none"/>
  </svg>
</section>

<section class="projects">
  <div class="section-eyebrow">Just A Few</div>
  <h2 class="display section-title">PROJECTS</h2>
  <div class="project-grid">
    <div class="tile" role="img" aria-label="3D render of a campus building and lawn" style="background:radial-gradient(ellipse 40% 25% at 50% 45%,#b4584a 0,transparent 100%),linear-gradient(180deg,#a8c6e6 0,#cfe0ef 35%,#9fb08a 62%,#6f8a4e 100%)"></div>
    <div class="tile" role="img" aria-label="Elf character beside a holiday slot game" style="background:radial-gradient(ellipse 35% 40% at 72% 55%,#d04a2e 0,transparent 100%),radial-gradient(ellipse 30% 50% at 25% 50%,#5a9a3a 0,transparent 100%),linear-gradient(135deg,#3a2a1e,#8a2e22)"></div>
    <div class="tile" role="img" aria-label="Animated old man with white mustache" style="background:radial-gradient(ellipse 35% 30% at 50% 40%,#e8e2dc 0,transparent 100%),radial-gradient(ellipse 45% 35% at 50% 85%,#3a3030 0,transparent 100%),linear-gradient(180deg,#8a807c,#4e4644)"></div>
    <div class="tile" role="img" aria-label="Illustrated guide title card with forest characters" style="background:radial-gradient(ellipse 45% 60% at 75% 45%,#9a6a3a 0,transparent 100%),radial-gradient(ellipse 35% 35% at 20% 70%,#6ea34a 0,transparent 100%),linear-gradient(135deg,#5a8a3a,#7a4e2a)"></div>
    <div class="tile" role="img" aria-label="Costumed mascots holding a parade banner" style="background:radial-gradient(ellipse 45% 25% at 40% 75%,#c0569a 0,transparent 100%),radial-gradient(ellipse 30% 40% at 30% 40%,#8a6040 0,transparent 100%),linear-gradient(180deg,#8fb6e0,#b8b0a8 55%,#5a5a60)"></div>
    <div class="tile" role="img" aria-label="Pencil sketch of a city skyline" style="background:radial-gradient(ellipse 40% 50% at 50% 40%,#8a8a8a 0,transparent 100%),linear-gradient(180deg,#f0f0f0,#b4b4b4 60%,#7a7a7a)"></div>
    <div class="tile" role="img" aria-label="Blue painted fantasy city at night" style="background:radial-gradient(ellipse 35% 45% at 55% 35%,#7a8af0 0,transparent 100%),radial-gradient(ellipse 50% 25% at 40% 85%,#141450 0,transparent 100%),linear-gradient(180deg,#3a4ad0,#22227a)"></div>
    <div class="tile" role="img" aria-label="Black and white storyboard panels" style="background:linear-gradient(90deg,#cfcfcf 0 48%,#f4f4f4 48% 52%,#a8a8a8 52%),linear-gradient(180deg,#ddd,#777)"></div>
  </div>
</section>

<section class="cta">
  <div class="media" style="left:112px;top:102px;width:436px;height:301px;background:
    radial-gradient(ellipse 22% 30% at 22% 40%,#c8926e 0,transparent 100%),
    radial-gradient(ellipse 22% 30% at 68% 45%,#b07a58 0,transparent 100%),
    radial-gradient(ellipse 60% 25% at 50% 90%,#e8e4de 0,transparent 100%),
    linear-gradient(180deg,#3a3028 0,#6b5a4a 45%,#2e3440 100%)" role="img" aria-label="Two studio founders smiling at a table"></div>
  <div class="abs" style="left:637px;top:106px;width:460px">
    <div class="eyebrow">Why Wait Let's Co-Create!</div>
    <h2 class="display title">ACHiEVE MORE WiTH A SMiLE!</h2>
    <p class="copy">No need to scroll, save your finger and drop us a line, When Is NOW A Good Time To Write? changed a lot over the years.</p>
    <a class="btn">CONTACT US</a>
  </div>
</section>

<section class="expertise">
  <div class="section-eyebrow">Creative Experts That Solve Problems</div>
  <h2 class="display section-title">OUR EXPERTiSE</h2>
  <div class="cards">
    <article class="card">
      <div class="card-icon" role="img" aria-label="Cartoon monster cooking up ideas" style="width:100px"></div>
      <h3 class="display">iP CREATiON</h3>
      <p>Developing, Directing and Selling captivating stories is in our DNA. Check what we are cooking up.</p>
    </article>
    <article class="card">
      <div class="card-icon" role="img" aria-label="Cartoon monster beside storyboard frames" style="width:180px"></div>
      <h3 class="display">STORY</h3>
      <p>From Storyboarding, to Story Consulting, and Script Doctoring, PM turns your stories into attention making monsters!</p>
    </article>
    <article class="card">
      <div class="card-icon" role="img" aria-label="Cartoon monster drawing motion lines" style="width:200px"></div>
      <h3 class="display">ANiMATiON</h3>
      <p>Pound for Pound we have worlds best animators and pride ourselves on the quality level we deliver.</p>
    </article>
    <article class="card">
      <div class="card-icon" role="img" aria-label="Cartoon monster in a rig pose" style="width:160px"></div>
      <h3 class="display">3D RiGGinG</h3>
      <p>Creating Feature level robust rigs to game and real time rigs with dynamics.</p>
    </article>
    <article class="card is-active">
      <div class="card-icon" role="img" aria-label="Cartoon monster with character sketches" style="width:170px"></div>
      <h3 class="display">CHARACTER DESiGn</h3>
      <p>Designing premier characters from concept to finished packets for 3D Development.</p>
    </article>
    <article class="card">
      <div class="card-icon" role="img" aria-label="Cartoon monster painting at an easel" style="width:150px"></div>
      <h3 class="display">ViS DEV</h3>
      <p>Building worlds and settings to enrich the places characters play. Saying more with an image.</p>
    </article>
  </div>
</section>

<footer class="site-footer">
  <div class="footer-brand">Pebblemoat</div>
  <p class="footer-about">Cooking up incredible home-grown stories that entertain the world! Pebblemoat Films is your TURN-KEY virtual creative solution to any problem.</p>
  <ul class="footer-col" style="left:521px"><h4>Quick Links</h4><li>Home</li><li>About us</li><li>Our Expertise</li><li>Project</li></ul>
  <ul class="footer-col" style="left:750px"><h4>Community</h4><li>Log In</li><li>Signin</li><li>Condition</li><li>Contact</li></ul>
  <ul class="footer-col" style="left:987px"><h4>Help Links</h4><li>FAQ</li><li>Support</li><li>Terms</li><li>Contact us</li></ul>
  <div class="footer-rule"></div>
  <div class="copyright">Copyrights@2022Pebblemoat.All Rights Reserved</div>
  <div class="socials">
    <span class="social" aria-label="Social profile"></span>
    <span class="social" aria-label="Social profile"></span>
    <span class="social" aria-label="Social profile"></span>
    <span class="social" aria-label="Social profile"></span>
  </div>
</footer>

</body>
</html>
```